Business Card Design for company

We want new business cards. We'd like something different-- yet still highly professional. Our tagline is Providing leadership, delivering success. Stock photos are ok, as long as they are relevant and look upscale.

Target Market(s)

Architecture/Business Management Consulting/Engineering Consulting

Contact Information for Business Card

dark gray background with pops of blue might be good, but you tell me. You're the designers. Rounded corners might be nice, but again, you tell me.

Font styles to use
Serif
Sans Serif

Colors
3276b5
5c5c5c
9d9d9d
fbfbfb

Requirements
Nice to have
• Something different, but still very professional.

```html
<!DOCTYPE html>
<html lang="en">
<head>
<meta charset="utf-8">
<title>Norvale Group — Business Card</title>
<link rel="stylesheet" href="https://fonts.googleapis.com/css2?family=Oswald:wght@500&family=Work+Sans:wght@400;500;600&display=swap">
<style>
  :root {
    --stage: #161616;
    --card: #262626;
    --card-edge: #303030;
    --blue: #3276b5;
    --mid-gray: #5c5c5c;
    --light-gray: #9d9d9d;
    --white: #fbfbfb;
  }
  * { box-sizing: border-box; margin: 0; padding: 0; }
  html, body { width: 1200px; height: 900px; overflow: hidden; }
  body {
    background: var(--stage);
    font-family: "Work Sans", Arial, sans-serif;
    color: var(--white);
    position: relative;
  }
  .card {
    position: absolute;
    left: 285px;
    width: 630px;
    height: 360px;
    background: linear-gradient(135deg, #2a2a2a 0%, var(--card) 60%, #222 100%);
    border: 1px solid var(--card-edge);
    box-shadow: 0 14px 30px rgba(0,0,0,.55);
  }
  .card--front { top: 70px; }
  .card--back { top: 470px; }

  /* Front */
  .wordmark {
    position: absolute;
    top: 120px;
    left: 0;
    width: 100%;
    text-align: center;
    font-weight: 600;
    font-size: 46px;
    letter-spacing: 4px;
    color: var(--light-gray);
    text-transform: uppercase;
  }
  .front-web {
    position: absolute;
    top: 268px;
    left: 0;
    width: 100%;
    display: flex;
    align-items: center;
    justify-content: center;
    gap: 14px;
    font-size: 13px;
    letter-spacing: .5px;
    color: var(--mid-gray);
  }
  .front-web .rule { width: 110px; height: 1px; background: var(--mid-gray); }

  /* Back */
  .identity {
    position: absolute;
    top: 128px;
    right: 335px;
    text-align: right;
  }
  .identity__name {
    font-family: "Oswald", "Arial Narrow", sans-serif;
    font-weight: 500;
    font-size: 34px;
    letter-spacing: 1.5px;
    color: var(--blue);
    text-transform: uppercase;
    line-height: 1.1;
  }
  .identity__role { font-size: 15px; margin-top: 6px; }
  .divider {
    position: absolute;
    top: 130px;
    left: 312px;
    width: 2px;
    height: 72px;
    background: var(--white);
  }
  .contacts {
    position: absolute;
    top: 128px;
    left: 336px;
    list-style: none;
    font-size: 15.5px;
    line-height: 26px;
  }
  .contacts li { display: flex; align-items: center; gap: 10px; }
  .contacts svg { width: 11px; height: 11px; flex: none; }
  .address {
    position: absolute;
    left: 150px;
    bottom: 48px;
    font-size: 15.5px;
    letter-spacing: .4px;
  }
</style>
</head>
<body>
  <section class="card card--front" aria-label="Card front">
    <div class="wordmark">Norvale Group</div>
    <div class="front-web"><span class="rule"></span><span>www.norvalegroup.com</span><span class="rule"></span></div>
  </section>

  <section class="card card--back" aria-label="Card back">
    <div class="identity">
      <div class="identity__name">Daniel Brooks</div>
      <div class="identity__role">Director</div>
    </div>
    <div class="divider"></div>
    <ul class="contacts">
      <li>
        <svg viewBox="0 0 12 12" aria-hidden="true"><path d="M2.5 1l2 2.2-1 1.2a7 7 0 0 0 4.1 4.1l1.2-1 2.2 2-1.2 1.5C5.5 11 1 6.5 1 2.2z" fill="var(--blue)"/></svg>
        <span>(555) 014-2290</span>
      </li>
      <li>
        <svg viewBox="0 0 12 12" aria-hidden="true"><rect x="1" y="2.5" width="10" height="7" fill="none" stroke="var(--blue)" stroke-width="1.2"/><path d="M1 3l5 3.5L11 3" fill="none" stroke="var(--blue)" stroke-width="1.2"/></svg>
        <span>info@norvalegroup.com</span>
      </li>
      <li>
        <svg viewBox="0 0 12 12" aria-hidden="true"><circle cx="6" cy="6" r="5" fill="none" stroke="var(--blue)" stroke-width="1.1"/><ellipse cx="6" cy="6" rx="2.2" ry="5" fill="none" stroke="var(--blue)" stroke-width="1"/><path d="M1 6h10" stroke="var(--blue)" stroke-width="1"/></svg>
        <span>www.norvalegroup.com</span>
      </li>
    </ul>
    <div class="address">212b Harlow Street, Fairmont, NZ, 4020</div>
  </section>
</body>
</html>
```